Thornvale Group needs a business card design

We need a new business card design using the logo recently selected in a logo competition on Pixel Bazaar. Our business is a consultancy specializing in aviation and energy and the winning business card design will promote an image of precision and professionalism with creativity.

Please use the logo with the name on the front of the card and use a complementary font. Make the back white with either the light grey or dark grey logo.

Target Market(s)

Senior finance and legal leaders at aviation and energy companies

Industry/Entity Type

Management Consulting

Contact Information for Business Card

Peter Castrell
President
Thornvale Group

www.thornvalegroup.example

(555) 204-6391
pc@thornvalegroup.example

Requirements
Must have
• Professional font that goes well with the logo font

```html
<!DOCTYPE html>
<html lang="en">
<head>
<meta charset="utf-8">
<title>Thornvale Group — Business Card</title>
<link rel="stylesheet" href="https://fonts.googleapis.com/css2?family=Open+Sans:wght@400;700&display=swap">
<style>
  :root {
    --bg: #ecedf0;
    --card-white: #ffffff;
    --lavender-top: #e4e6f0;
    --lavender-bottom: #b7bbd3;
    --blue-light: #4f87ad;
    --blue-dark: #1c4a76;
    --brand-blue: #2b5c86;
    --text-grey: #8a8d96;
    --slate-top: #6a6f74;
    --slate-bottom: #2b2f33;
    --brand-light: #e6e9f2;
  }
  * { box-sizing: border-box; margin: 0; padding: 0; }
  html, body { width: 1200px; height: 913px; overflow: hidden; }
  body {
    background: var(--bg);
    font-family: "Open Sans", Arial, sans-serif;
    position: relative;
  }
  .card {
    position: absolute;
    width: 525px;
    height: 300px;
    border-radius: 16px;
    overflow: hidden;
    box-shadow: 0 10px 28px rgba(0,0,0,0.18);
  }
  .card-front { left: 60px; top: 130px; background: var(--card-white); }
  .card-back { left: 615px; top: 483px; background: linear-gradient(180deg, var(--slate-top), var(--slate-bottom)); }
  .card-shapes { position: absolute; inset: 0; width: 100%; height: 100%; }

  .holder { position: absolute; left: 34px; top: 150px; }
  .holder-name { font-weight: 700; font-size: 22px; color: var(--brand-blue); line-height: 1.1; }
  .holder-title { font-size: 14px; color: var(--text-grey); margin-top: 2px; }

  .brand-name {
    font-family: "Open Sans", Arial, sans-serif;
    font-weight: 400;
    line-height: 1.2;
    white-space: nowrap;
  }
  .card-front .brand-name {
    position: absolute; right: 30px; top: 80px;
    font-size: 20px; color: var(--brand-blue);
  }
  .card-back .brand-name {
    position: absolute; left: 0; right: 0; top: 205px;
    text-align: center;
    font-size: 32px; color: var(--brand-light);
  }

  .contact {
    position: absolute; right: 30px; top: 162px;
    list-style: none; text-align: right;
    font-size: 13.5px; color: var(--brand-blue); line-height: 1.55;
  }
  .contact li { display: flex; justify-content: flex-end; align-items: center; gap: 6px; }
  .contact li.gap { margin-top: 10px; }
  .contact svg { width: 11px; height: 11px; fill: none; stroke: var(--text-grey); stroke-width: 1.6; }
</style>
</head>
<body>

<section class="card card-front">
  <svg class="card-shapes" viewBox="0 0 525 300" preserveAspectRatio="none" aria-hidden="true">
    <defs>
      <linearGradient id="frontLavender" x1="0" y1="0" x2="0" y2="1">
        <stop offset="0" stop-color="var(--lavender-top)"/>
        <stop offset="1" stop-color="var(--lavender-bottom)"/>
      </linearGradient>
      <linearGradient id="frontBlue" x1="0" y1="0" x2="0" y2="1">
        <stop offset="0" stop-color="var(--blue-light)"/>
        <stop offset="1" stop-color="var(--blue-dark)"/>
      </linearGradient>
    </defs>
    <polygon points="0,0 190,0 262,300 0,300" fill="url(#frontLavender)"/>
    <polygon points="190,0 330,0 262,300" fill="url(#frontBlue)"/>
  </svg>

  <div class="holder">
    <p class="holder-name">Peter Castrell</p>
    <p class="holder-title">President</p>
  </div>

  <h1 class="brand-name">Thornvale Group</h1>

  <ul class="contact">
    <li>(555) 204-6391
      <svg viewBox="0 0 12 12"><path d="M2 1.5l2 0 1 3-1.3 1a6 6 0 0 0 2.8 2.8l1-1.3 3 1v2c0 .6-.4 1-1 1A9.5 9.5 0 0 1 1 2.5c0-.6.4-1 1-1z"/></svg>
    </li>
    <li class="gap">pc@thornvalegroup.example
      <svg viewBox="0 0 12 12"><rect x="1" y="2.5" width="10" height="7"/><path d="M1 2.5l5 4 5-4"/></svg>
    </li>
    <li>www.thornvalegroup.example
      <svg viewBox="0 0 12 12"><circle cx="6" cy="6" r="5"/><path d="M1 6h10M6 1c-2.5 3-2.5 7 0 10M6 1c2.5 3 2.5 7 0 10"/></svg>
    </li>
  </ul>
</section>

<section class="card card-back">
  <svg class="card-shapes" viewBox="0 0 525 300" preserveAspectRatio="none" aria-hidden="true">
    <defs>
      <linearGradient id="backBlue" x1="0" y1="0" x2="1" y2="1">
        <stop offset="0" stop-color="var(--blue-light)"/>
        <stop offset="1" stop-color="var(--blue-dark)"/>
      </linearGradient>
    </defs>
    <polygon points="150,0 525,0 525,150" fill="url(#backBlue)"/>
    <polygon points="150,0 525,150 525,172 0,160 0,40" fill="var(--lavender-top)"/>
  </svg>

  <p class="brand-name">Thornvale Group</p>
</section>

</body>
</html>
```